TL - business card

Tallow Partners is an insurance brokerage firm, inovative, proactive, vigorous, which aims to become the leader of the insurance brokers in Anfrica. We should like to get some designs which should be avoided also in Gray / Metallic for the Administration and Orange / Blue for the Managers (ike in the picture sent). The Blue / Green logo is not the correct one, but the source of the file. Please adjust the color accordingly for the business cards. 1 / Orange / Blue 2 / Gray / Metallic We want something classic but which is transmitted strenght, inovation, modernity and most of all, rapidity. We want something start-up like, very punchy and catching eye remaining profesional at the same time. Name: Dorian Whitlock Function: Managing Director Address: N ° 17/18 Rua Veloso - R / C 2B Direita - Bairro Mutamba - Luanda Tel: (+244) 947 582 316 Email: dorian.whitlock@tallow-p.example Website: www.tallow-p. example We want classic in the front and creative, colorfull at the back. The cards will be printed in relief, with very high quality of paper.
Insurance Broker
Colors
Designer to choose colors to be used in the design.

```html
<!DOCTYPE html>
<html lang="en">
<head>
<meta charset="utf-8">
<title>Tallow Partners – Business Card</title>
<link rel="stylesheet" href="https://fonts.googleapis.com/css2?family=Roboto:wght@400;500;700&display=swap">
<style>
  :root {
    --bg: #2b2b2d;
    --green: #0e9640;
    --blue: #2ba8e2;
    --white: #ffffff;
    --ink: #3a3a3a;
  }
  html, body {
    margin: 0;
    width: 1200px;
    height: 960px;
    overflow: hidden;
    background: var(--bg);
    font-family: "Roboto", Arial, sans-serif;
  }
  .canvas {
    position: relative;
    width: 1200px;
    height: 960px;
  }
  .card {
    position: absolute;
    left: 250px;
    width: 700px;
    height: 400px;
    overflow: hidden;
    background: var(--white);
    box-shadow: 0 10px 30px rgba(0,0,0,.45);
  }
  .card--back { top: 50px; }
  .card--front { top: 500px; background: var(--green); }

  /* back */
  .back-brand {
    position: absolute;
    inset: 0;
    display: flex;
    flex-direction: column;
    align-items: center;
    justify-content: center;
    gap: 22px;
  }
  .brand-mark {
    display: flex;
    align-items: center;
    gap: 12px;
  }
  .brand-dot {
    width: 22px;
    height: 22px;
    border-radius: 50%;
    background: var(--blue);
  }
  .brand-name {
    font-weight: 700;
    color: var(--green);
    text-transform: uppercase;
    letter-spacing: .5px;
  }
  .back-brand .brand-name { font-size: 40px; }
  .back-url {
    font-size: 15px;
    letter-spacing: 6px;
    color: var(--ink);
  }

  /* front */
  .front-shape {
    position: absolute;
    inset: 0;
  }
  .holder {
    position: absolute;
    left: 56px;
    top: 92px;
    color: var(--white);
  }
  .holder-name { margin: 0; font-size: 28px; font-weight: 700; }
  .holder-role { margin: 2px 0 0; font-size: 16px; font-weight: 500; }
  .address {
    position: absolute;
    left: 76px;
    top: 200px;
    margin: 0;
    font-style: normal;
    font-size: 16px;
    line-height: 1.35;
    color: var(--white);
  }
  .contacts {
    position: absolute;
    left: 56px;
    top: 282px;
    margin: 0;
    padding: 0;
    list-style: none;
    font-size: 17px;
    line-height: 1.5;
    color: var(--white);
  }
  .contacts li { display: flex; align-items: center; gap: 8px; }
  .contacts svg { width: 14px; height: 14px; fill: var(--white); flex: none; }
  .front-brand {
    position: absolute;
    left: 470px;
    top: 170px;
    width: 220px;
    display: flex;
    justify-content: center;
  }
  .front-brand .brand-name { font-size: 22px; }
  .front-brand .brand-dot { width: 14px; height: 14px; }
</style>
</head>
<body>
<div class="canvas">

  <section class="card card--back" aria-label="Card back">
    <div class="back-brand">
      <div class="brand-mark">
        <span class="brand-dot"></span>
        <span class="brand-name">Tallow Partners</span>
      </div>
      <div class="back-url">www.tallow-p. example</div>
    </div>
  </section>

  <section class="card card--front" aria-label="Card front">
    <svg class="front-shape" viewBox="0 0 700 400" width="700" height="400" aria-hidden="true">
      <path d="M452 0 L700 0 L700 400 L524 400 C380 345 362 110 452 0 Z" fill="var(--blue)"/>
      <path d="M462 0 L700 0 L700 400 L540 400 C394 345 374 110 462 0 Z" fill="var(--white)"/>
    </svg>

    <header class="holder">
      <h1 class="holder-name">Dorian Whitlock</h1>
      <p class="holder-role">Managing Director</p>
    </header>

    <address class="address">
      N ° 17/18 Rua Veloso<br>
      R / C 2B Direita<br>
      Bairro Mutamba, Luanda
    </address>

    <ul class="contacts">
      <li>
        <svg viewBox="0 0 24 24"><path d="M6.6 10.8a15 15 0 0 0 6.6 6.6l2.2-2.2c.3-.3.7-.4 1-.2 1.1.4 2.3.6 3.6.6.6 0 1 .4 1 1V20c0 .6-.4 1-1 1A17 17 0 0 1 3 4c0-.6.4-1 1-1h3.5c.6 0 1 .4 1 1 0 1.3.2 2.5.6 3.6.1.3 0 .7-.2 1z"/></svg>
        (+244) 947 582 316
      </li>
      <li>
        <svg viewBox="0 0 24 24"><path d="M2 5h20v14H2z M4 7v.5l8 5 8-5V7l-8 5z" fill-rule="evenodd"/></svg>
        dorian.whitlock@tallow-p.example
      </li>
      <li>
        <svg viewBox="0 0 24 24"><circle cx="12" cy="12" r="10"/></svg>
        www.tallow-p. example
      </li>
    </ul>

    <div class="front-brand">
      <div class="brand-mark">
        <span class="brand-dot"></span>
        <span class="brand-name">Tallow Partners</span>
      </div>
    </div>
  </section>

</div>
</body>
</html>
```